Torvel’s letterhead for local government

I require a letterhead for quarterly communications with constituents. The colours I have used in the past are navy & green (together) so I’m happy to use similar colours for this. Please refer to business card as an example.
The letter must make reference to the position I hold which is as per below
“Clr Torvel Quennisbury OAM”
And the tag line I have used in the past is “Torvel on the Terrace”. Although I’m not sure if this would be used in a letterhead or not. Happy for this to be provided as an option.
I would like a photo in the letterhead as I believe face recognition is key as an elected member.

Target Market(s)

Political interests

Industry/Entity Type

Government Office

Font styles to use
Sans Serif

Requirements
Must have
• Politically professional. I have been an elected member for 2 years so it is expected that the letterhead conveys that. The colours of the business card is to be used.
Nice to have
• Background of photos to be manipulated or changed to make me stand out, if possible?
Should not have
• Looked like it’s cropped or undertaken by an amateur designer.

```html
<!DOCTYPE html>
<html lang="en">
<head>
<meta charset="utf-8">
<title>Torvel Quennisbury – Letterhead</title>
<link rel="stylesheet" href="https://fonts.googleapis.com/css2?family=Arimo:wght@400;700&family=Open+Sans:wght@400;600&display=swap">
<style>
  :root {
    --navy: #2b5d91;
    --green: #45b86a;
    --paper: #ffffff;
    --ink: #3f3f3f;
    --backdrop: #e4e4e4;
    --photo-dark: #3a3f4a;
    --photo-light: #8c96a6;
  }
  * { box-sizing: border-box; margin: 0; padding: 0; }
  html, body {
    width: 1040px; height: 1200px; overflow: hidden;
    background: var(--backdrop);
  }
  .letterhead {
    position: absolute; left: 70px; top: 21px;
    width: 900px; height: 1158px;
    background: var(--paper);
    box-shadow: 0 2px 10px rgba(0,0,0,0.18);
    font-family: "Open Sans", sans-serif;
    color: var(--ink);
    overflow: hidden;
  }
  .masthead { position: absolute; left: 0; top: 0; width: 900px; height: 205px; }
  .masthead svg { display: block; }
  .councillor-name {
    position: absolute; left: 270px; top: 70px;
    font-family: "Arimo", sans-serif; font-weight: 700;
    font-size: 25px; color: var(--green); letter-spacing: 0.1px;
  }
  .councillor-role {
    position: absolute; left: 270px; top: 110px;
    font-family: "Arimo", sans-serif; font-size: 19.5px;
    line-height: 24px; color: #ffffff;
  }
  .letter-body {
    position: absolute; left: 84px; width: 728px;
    font-size: 14px; line-height: 17.5px;
  }
  .issue-date { top: 243px; }
  .recipient { top: 278px; }
  .salutation { top: 380px; }
  .letter-text { top: 432px; }
  .letter-text p {
    text-align: justify; hyphens: auto;
    line-height: 26px; margin-bottom: 26px;
  }
  .closing { top: 820px; }
  .signatory-name {
    position: absolute; left: 84px; top: 896px;
    font-size: 17px; font-weight: 600; color: #333;
  }
  .signatory-title {
    position: absolute; left: 84px; top: 926px; font-size: 14px;
  }
  .contact-bar {
    position: absolute; left: 0; bottom: 0; width: 900px; height: 59px;
    background: var(--green); color: #ffffff;
    font-family: "Arimo", sans-serif; font-size: 17.5px;
    display: flex; align-items: center; justify-content: center; gap: 14px;
  }
  .contact-bar strong { font-weight: 700; }
  .contact-bar .divider { opacity: 0.9; }
</style>
</head>
<body>
  <main class="letterhead">
    <header class="masthead">
      <svg width="900" height="205" viewBox="0 0 900 205">
        <defs>
          <linearGradient id="portraitTone" x1="0" y1="0" x2="0" y2="1">
            <stop offset="0" stop-color="var(--photo-light)"/>
            <stop offset="1" stop-color="var(--photo-dark)"/>
          </linearGradient>
        </defs>
        <polygon points="0,0 900,0 900,156 0,204" fill="var(--navy)"/>
        <polygon points="0,204 900,156 900,198" fill="var(--green)"/>
        <rect role="img" aria-label="Portrait photo of Clr Torvel Quennisbury in a dark suit and tie"
              x="79" y="17" width="151" height="183" rx="4" fill="url(#portraitTone)"/>
      </svg>
      <div class="councillor-name">Clr Torvel Quennisbury OAM</div>
      <div class="councillor-role">Candidate for Area Councillor<br>City of Marrowby</div>
    </header>

    <div class="letter-body issue-date">Issuing Date: May 5, 2018</div>
    <div class="letter-body recipient">Name Of Employee Mr. XYZABC<br>Address of Employee<br>Address Line 2 etc..</div>
    <div class="letter-body salutation">Dear Mr.XYZABC</div>

    <div class="letter-body letter-text">
      <p>Lorem Ipsum has been the industry's standard dummy text ever since the 1500s, when an unknown printer took a galley of type and scrambled it to make a type specimen book. It has survived not only five centuries, but also the leap into electronic typesetting, remaining essentially unchanged. It was popularised in the 1960s with the release of Plimwick sheets containing Lorem Ipsum passages, and more recently with desktop publishing software like Corvane PageSmith including versions of Lorem Ipsum.</p>
      <p>Lorem Ipsum is simply dummy text of the printing and typesetting industry. Lorem Ipsum has been the industry's standard dummy text ever since the 1500s, when an unknown printer took a galley of type and scrambled it to make a type specimen book.</p>
      <p>It has survived not only five centuries, but also the leap into electronic typesetting, remaining essentially unchanged. It was popularised in the 1960s with the release of Plimwick sheets containing Lorem IpsumIpsum passages.</p>
    </div>

    <div class="letter-body closing">Yours Sincerely</div>
    <div class="signatory-name">Dorian Feltwell</div>
    <div class="signatory-title">Managing Director</div>

    <footer class="contact-bar">
      <span><strong>P:</strong> 044-987 650 321</span>
      <span class="divider">|</span>
      <span><strong>E:</strong> info@quennisbury-office.com</span>
      <span class="divider">|</span>
      <span>www.quennisbury-office.com</span>
    </footer>
  </main>
</body>
</html>
```